DRUM needs a contemporary simple brochure

We help companies understand their customers, and we would like to send a minimalistic card/brochure to potential clients to introduce our company. The card will be A6 in size (ie A5 folded once) and so will have a front, an inside front, and inside back, and a back page. It can either be portrait or landscape.
It should convey contemporary/modern, bold, fun, uncomplicated/simplicity, be clean/uncluttered, and use friendly and easy to read fonts.
Attached is the information the brochure/card should contain, together with colour palatte and another document which shows our logo, existing stationary etc to give you a feel of the brand. The background of the card could be black, yellow or white (or a combination). thanks, mark
Updates
Hi everyone. Just to let you know that the card will be A6 size, will have a matt laminate finish and can include spot uv. thanks, mark
Reason: Hi, I am looking for some better quality designs so i have extended the deadline and significantly increased the budget. thanks, mark
Target Market(s)
Marketing professionals in large corporates
Industry/Entity Type
It Company
Requirements
Must have
- use our company colours (attached)

```html
<!DOCTYPE html>
<html lang="en">
<head>
<meta charset="utf-8">
<title>DRUM – Customer &amp; Shopper Market Research Brochure</title>
<link href="https://fonts.googleapis.com/css2?family=Arimo:wght@400;700&display=swap" rel="stylesheet">
<style>
  :root {
    --page-bg: #e9e4dc;
    --panel: #3b3a3b;
    --accent: #f7c600;
    --ink: #111111;
    --label: #3b3a3b;
    --frame: #ffffff;
    --photo-light: #eef0f2;
    --photo-mid: #b9b2aa;
    --photo-dark: #3d4656;
  }
  * { margin: 0; padding: 0; box-sizing: border-box; }
  html, body {
    width: 1200px; height: 1141px; overflow: hidden;
    background: var(--page-bg);
    font-family: "Arimo", Arial, sans-serif;
  }
  .spread { position: relative; width: 1200px; height: 1141px; }
  .panel {
    position: absolute; top: 19px; height: 1056px;
    background: var(--panel); color: var(--accent); font-weight: 700;
  }
  .panel--services { left: 17px; width: 573px; }
  .panel--about { left: 604px; width: 578px; }

  .services-title {
    position: absolute; left: 38px; top: 44px;
    font-size: 24px; font-weight: 700; white-space: nowrap;
  }
  .service-list { list-style: none; }
  .service-item {
    position: absolute; display: flex; align-items: center; gap: 16px;
    font-size: 18px; white-space: nowrap;
  }
  .service-item svg { width: 23px; height: 23px; flex: none; }

  .photo {
    position: absolute; left: 15px; width: 537px; height: 197px;
    border: 2px solid var(--frame);
  }
  .photo--welcome { top: 389px; background: linear-gradient(100deg, var(--photo-light) 0%, #f3e6df 45%, var(--photo-mid) 100%); }
  .photo--communities { top: 605px; background: linear-gradient(100deg, var(--photo-dark) 0%, #8c8f98 45%, #f1f2f4 70%, var(--photo-dark) 100%); }
  .photo--experience { top: 823px; background: linear-gradient(100deg, #e6e6e6 0%, #c6a88f 35%, #8a8478 70%, #4b4c50 100%); }
  .photo-caption {
    position: absolute; font-size: 23px; font-weight: 700; white-space: nowrap;
  }
  .photo-caption--dark { color: var(--ink); }
  .photo-caption--accent { color: var(--accent); }
  .welcome-line { position: absolute; font-size: 23px; color: var(--ink); white-space: nowrap; }

  .brand-name {
    position: absolute; left: 18px; top: 52px;
    font-size: 40px; line-height: 48px; font-weight: 700;
  }
  .copy {
    position: absolute; font-size: 23.5px; line-height: 28px; white-space: nowrap;
  }
  .tagline { position: absolute; left: 15px; top: 880px; font-size: 31px; white-space: nowrap; }
  .web-link { position: absolute; left: 18px; top: 930px; font-size: 21px; white-space: nowrap; }

  .side-label {
    position: absolute; left: 0; width: 1200px; top: 1078px;
    text-align: center; font-size: 56px; line-height: 62px; font-weight: 700;
    color: var(--label);
  }
</style>
</head>
<body>
<main class="spread">

  <section class="panel panel--services">
    <h2 class="services-title">Customer &amp; Shopper Market Research</h2>
    <ul class="service-list">
      <li class="service-item" style="left:27px;top:114px"><svg viewBox="0 0 24 24"><circle cx="12" cy="12" r="11" fill="var(--accent)"/><path d="M9 7 L17 12 L9 17 Z" fill="var(--panel)"/></svg>New Product Development</li>
      <li class="service-item" style="left:336px;top:114px"><svg viewBox="0 0 24 24"><circle cx="12" cy="12" r="11" fill="var(--accent)"/><path d="M9 7 L17 12 L9 17 Z" fill="var(--panel)"/></svg>Online Communities</li>
      <li class="service-item" style="left:27px;top:180px"><svg viewBox="0 0 24 24"><circle cx="12" cy="12" r="11" fill="var(--accent)"/><path d="M9 7 L17 12 L9 17 Z" fill="var(--panel)"/></svg>Product Testing</li>
      <li class="service-item" style="left:336px;top:180px"><svg viewBox="0 0 24 24"><circle cx="12" cy="12" r="11" fill="var(--accent)"/><path d="M9 7 L17 12 L9 17 Z" fill="var(--panel)"/></svg>Customer Experience</li>
      <li class="service-item" style="left:27px;top:244px"><svg viewBox="0 0 24 24"><circle cx="12" cy="12" r="11" fill="var(--accent)"/><path d="M9 7 L17 12 L9 17 Z" fill="var(--panel)"/></svg>Retail</li>
      <li class="service-item" style="left:336px;top:244px"><svg viewBox="0 0 24 24"><circle cx="12" cy="12" r="11" fill="var(--accent)"/><path d="M9 7 L17 12 L9 17 Z" fill="var(--panel)"/></svg>Visualisation</li>
      <li class="service-item" style="left:27px;top:310px"><svg viewBox="0 0 24 24"><circle cx="12" cy="12" r="11" fill="var(--accent)"/><path d="M9 7 L17 12 L9 17 Z" fill="var(--panel)"/></svg>Customer Segmentation</li>
      <li class="service-item" style="left:336px;top:310px"><svg viewBox="0 0 24 24"><circle cx="12" cy="12" r="11" fill="var(--accent)"/><path d="M9 7 L17 12 L9 17 Z" fill="var(--panel)"/></svg>Bespoke Research</li>
    </ul>

    <div class="photo photo--welcome" role="img" aria-label="Photo of a smiling businesswoman in an office with colleagues blurred behind her">
      <span class="welcome-line" style="left:19px;top:20px">We</span>
      <span class="welcome-line" style="left:50px;top:42px">are</span>
      <span class="welcome-line" style="left:13px;top:70px">here for You !</span>
    </div>
    <div class="photo photo--communities" role="img" aria-label="Photo of three smiling business people looking at a screen together">
      <span class="photo-caption photo-caption--accent" style="right:18px;top:154px">Online Communities</span>
    </div>
    <div class="photo photo--experience" role="img" aria-label="Photo of a smiling businessman talking with a colleague">
      <span class="photo-caption photo-caption--dark" style="right:18px;top:152px">Customer Experience</span>
    </div>
  </section>

  <section class="panel panel--about">
    <span class="brand-name">DRUM</span>
    <p class="copy" style="left:19px;top:72px;text-indent:129px">is a progressive, technology friendly<br>market research agency, specialising in<br>customer and shopper research. We help<br>companies understand the ever-changing<br>relationships people have with media, services,<br>products and brands by combining innovative<br>methods, creative thinking, research expertise<br>and a deep understanding of shopper and<br>consumer decision-making.</p>
    <p class="copy" style="left:15px;top:334px;text-indent:106px">We offer cost effective research,<br>designed and managed by experienced<br>practitioners, using award winning online,<br>mobile, community and video based research<br>applications.</p>
    <p class="copy" style="left:19px;top:494px;text-indent:105px">Lorem ipsum dolor sit amet, consecte<br>dipisicing elit, sed do eiusmod tempor incididunt<br>ut labore et dolore magna aliqua.Ut enim ad<br>minim veniam, quis nostrud exercitation ullam<br>laboris nisi ut aliquip ex ea commodo consequa.<br>Lorem ipsum dolor sit amet,consectetur adipis<br>sed do eiusmod tempor incididunt ut labore et.</p>
    <p class="copy" style="left:19px;top:706px;text-indent:105px">Lorem ipsum dolor sit amet, consecte<br>dipisicing elit, sed do eiusmod tempor incididunt<br>ut labore et dolore magna aliqua.Ut enim ad<br>minim veniam, quis nostrud exercitation ullam<br>laboris nisi.</p>
    <h2 class="tagline">Understand your customers better</h2>
    <p class="web-link">find out more at www.drumresearch.com.au</p>
  </section>

  <p class="side-label">Inside</p>

</main>
</body>
</html>
```